Business Recognition Design

We need a design for a recognition to be given to business leaders in our community.
The recognition shall be made on a brass plaque on wood panel background (picture attached, please use it as a background), and all drawing must be in vectors and only one color (black).
It should also have a logo on the top and signature on the right bottom.
The text is enclosed in DOC file.
Updates

Reason: just to be able to find the best solution

Reason: None of the suggestion is good enough. Logo in general is too big in comparison with the rest of the plate.

Industry/Entity Type

Business

Requirements
Must have
• - standard Windows font (or possibility to install the same font on Windows), as the name on the recognition shall be printed in the same font
Nice to have
• - some graphic element (in curves) representing achievements in business
- should look great :)

```html
<!DOCTYPE html>
<html lang="en">
<head>
<meta charset="utf-8">
<title>Business Recognition Plaque</title>
<link rel="stylesheet" href="https://fonts.googleapis.com/css2?family=Noto+Sans:wght@400;700&display=swap">
<style>
  :root {
    --wood-light: #d07a3e;
    --wood-dark: #bf6530;
    --mount-outer: #6f4226;
    --mount-inner: #8a5835;
    --brass-light: #efd57c;
    --brass-mid: #dcb84e;
    --brass-dark: #c39a34;
    --brass-edge: #f6e6a6;
    --ink: #111111;
    --ribbon-text: #ffffff;
    --screw: #c9a23a;
  }
  html, body {
    margin: 0;
    padding: 0;
    overflow: hidden;
  }
  .canvas {
    position: relative;
    width: 1200px;
    height: 927px;
    overflow: hidden;
    font-family: "Noto Sans", Verdana, sans-serif;
    color: var(--ink);
  }
  .wood-backdrop {
    position: absolute;
    inset: 0;
    background: linear-gradient(90deg, var(--wood-dark), var(--wood-light) 50%, var(--wood-dark));
  }
  .wood-mount {
    position: absolute;
    left: 38px;
    top: 38px;
    width: 1122px;
    height: 864px;
    background: var(--mount-outer);
  }
  .wood-mount-face {
    position: absolute;
    left: 58px;
    top: 58px;
    width: 1082px;
    height: 824px;
    background: var(--mount-inner);
  }
  .brass-plate {
    position: absolute;
    left: 84px;
    top: 84px;
    width: 1026px;
    height: 768px;
    border: 2px solid var(--brass-edge);
    background: linear-gradient(100deg, var(--brass-dark), var(--brass-mid) 35%, var(--brass-light) 60%, var(--brass-mid) 85%, var(--brass-dark));
  }
  .plaque-lines {
    position: absolute;
    inset: 0;
  }
  .title-band {
    position: absolute;
    left: 395px;
    top: 152px;
    width: 407px;
    height: 71px;
    background: var(--ink);
  }
  .text-line {
    position: absolute;
    left: 0;
    width: 1200px;
    text-align: center;
    white-space: nowrap;
    line-height: 1;
  }
  .band-title {
    top: 158px;
    font-size: 47px;
    color: var(--ribbon-text);
    letter-spacing: 1.5px;
  }
  .logo-name {
    top: 322px;
    font-size: 68px;
    font-weight: 700;
    letter-spacing: 5px;
  }
  .award-title { top: 461px; font-size: 36px; letter-spacing: 1.4px; }
  .award-to { top: 509px; font-size: 36px; }
  .recipient { top: 557px; font-size: 36px; letter-spacing: 2.6px; }
  .recipient strong { font-weight: 700; }
  .citation {
    position: absolute;
    top: 629px;
    left: 0;
    width: 1200px;
    margin: 0;
    text-align: center;
    font-size: 27px;
    line-height: 37px;
    letter-spacing: 1.5px;
  }
  .citation strong { font-weight: 700; }
  .issue-date {
    position: absolute;
    left: 184px;
    top: 786px;
    font-size: 25px;
    line-height: 1;
    letter-spacing: 1.8px;
  }
  .issue-date sup { font-size: 14px; letter-spacing: 0; }
  .signatory {
    position: absolute;
    right: 204px;
    top: 786px;
    font-size: 25px;
    line-height: 1;
    letter-spacing: 1.3px;
  }
</style>
</head>
<body>
<main class="canvas">
  <div class="wood-backdrop" role="img" aria-label="Warm orange wood grain background"></div>
  <div class="wood-mount" role="img" aria-label="Dark walnut wood panel mount"></div>
  <div class="wood-mount-face"></div>
  <div class="brass-plate" role="img" aria-label="Brushed brass plate surface"></div>

  <svg class="plaque-lines" width="1200" height="927" viewBox="0 0 1200 927" aria-hidden="true">
    <defs>
      <radialGradient id="screw-head" cx="0.35" cy="0.35" r="0.7">
        <stop offset="0" stop-color="#fff2b0"/>
        <stop offset="0.5" stop-color="var(--screw)"/>
        <stop offset="1" stop-color="#7a5a14"/>
      </radialGradient>
    </defs>
    <path class="engraved-border" d="M142 118 H1068 A18 18 0 0 0 1086 136 V800 A18 18 0 0 0 1068 818 H142 A18 18 0 0 0 124 800 V136 A18 18 0 0 0 142 118 Z"
          fill="none" stroke="var(--ink)" stroke-width="3"/>
    <g class="screws">
      <circle cx="124" cy="118" r="14" fill="url(#screw-head)"/>
      <circle cx="1086" cy="118" r="14" fill="url(#screw-head)"/>
      <circle cx="124" cy="818" r="14" fill="url(#screw-head)"/>
      <circle cx="1086" cy="818" r="14" fill="url(#screw-head)"/>
    </g>
  </svg>

  <div class="title-band"></div>
  <div class="text-line band-title">RECOGNITION</div>
  <div class="text-line logo-name">(Your Logo)</div>
  <div class="text-line award-title">The Best Entrepreneur in 2013</div>
  <div class="text-line award-to">to</div>
  <div class="text-line recipient">Mr. <strong>Daniel R. Whitmore,</strong> MBA</div>
  <p class="citation">Under the leadership of Mr. Daniel R. Whitmore, MBA<br>
    the company <strong>DR-WHITMORE Ltd</strong> has been selected<br>
    by a City Council as the best company of The City.</p>
  <div class="issue-date">Date: 4<sup>th</sup> July, 2013</div>
  <div class="signatory">City Mayor</div>
</main>
</body>
</html>
```